physical therapy flyer

2 office locations speciality programs - work injury / Motor vehicle accidents - spanish speaking - do not put balance defecits/ fall prevention - Spanish speaking
neck and back pain shoulder pain/ rotator cuff disorder / bursitis
hip pain knee andle and foot pain post operative care including Spine , shoulder , knee , total joint replacement

Meadowlark Physical therapy & Chiropractic
4871 Pinecrest BLvd
dalton heights ny 10592
7185820147
3715 Tillman Parkway
Fernvale NY 10592
7189043218
www.meadowlarkptrehab.com

```html
<!DOCTYPE html>
<html lang="en">
<head>
<meta charset="utf-8">
<title>Meadowlark Physical Therapy &amp; Chiropractic – Trifold</title>
<link href="https://fonts.googleapis.com/css2?family=Poppins:wght@300;400;500;600;700&display=swap" rel="stylesheet">
<style>
  :root {
    --green-text: #3a8d3b;
    --green-dark: #22532f;
    --green-mid: #3a8a45;
    --green-light: #4aa548;
    --green-deep: #2e6e3e;
    --arrow: #1f4d2b;
    --paper: #ffffff;
    --paper-shade: #c6c7cb;
    --white-soft: #f2f2f2;
    --photo-1: #c9c3b8;
    --photo-2: #8fa7b8;
  }
  * { margin: 0; padding: 0; box-sizing: border-box; }
  html, body { width: 1200px; height: 880px; overflow: hidden; background: #ffffff; }
  .brochure {
    position: relative; width: 1200px; height: 880px; overflow: hidden;
    font-family: "Poppins", sans-serif;
  }
  .panel { position: absolute; top: 0; width: 400px; height: 880px; }
  .panel--left { left: 0; background: linear-gradient(90deg, var(--paper) 0%, #e8e8ea 55%, var(--paper-shade) 100%); }
  .panel--middle { left: 400px; background: linear-gradient(90deg, var(--paper) 0%, #e8e8ea 55%, var(--paper-shade) 100%); }
  .panel--right { left: 800px; background: var(--paper); }

  .photo {
    position: absolute; left: 800px; top: 0; width: 400px; height: 410px;
    background: linear-gradient(135deg, var(--photo-1) 0%, #d8d4cc 45%, var(--photo-2) 100%);
  }
  .waves { position: absolute; inset: 0; width: 1200px; height: 880px; }

  .programs-title {
    position: absolute; left: 0; width: 400px; top: 24px; text-align: center;
    color: var(--green-text); font-weight: 700; font-size: 28px; line-height: 34px;
  }
  .program-list { position: absolute; list-style: none; }
  .program-list--left { left: 42px; top: 136px; }
  .program-list--middle { left: 436px; top: 136px; }
  .program-list li {
    position: relative; padding-left: 29px; color: var(--green-text);
    font-weight: 600; font-size: 17.5px; line-height: 25px; margin-bottom: 11px;
  }
  .program-list--middle li { margin-bottom: 11.5px; }
  .program-list li::before {
    content: ""; position: absolute; left: 0; top: 4px;
    border-left: 16px solid var(--arrow);
    border-top: 8.5px solid transparent; border-bottom: 8.5px solid transparent;
  }

  .offices {
    position: absolute; left: 42px; top: 340px; width: 330px;
    display: flex; justify-content: space-between;
  }
  .office { color: var(--green-text); font-style: normal; font-size: 13px; line-height: 19px; font-weight: 500; }
  .office-name { display: block; font-weight: 700; font-size: 14px; margin-bottom: 2px; }

  .brand { position: absolute; left: 52px; top: 490px; display: flex; align-items: center; gap: 12px; }
  .brand-mark { width: 38px; height: 38px; border-radius: 50%; background: var(--green-text); flex: none; }
  .brand-name { color: var(--green-text); font-weight: 400; font-size: 17px; line-height: 20px; }
  .website {
    position: absolute; left: 0; width: 400px; top: 562px; text-align: center;
    color: var(--green-text); font-weight: 500; font-size: 19px;
  }

  .contact-title {
    position: absolute; left: 560px; width: 500px; top: 504px; text-align: center;
    color: var(--white-soft); font-weight: 700; font-size: 26.5px; line-height: 36px; letter-spacing: 0.5px;
  }
  .contact-body {
    position: absolute; left: 500px; width: 600px; top: 640px; text-align: center;
    color: var(--white-soft); font-weight: 300; font-size: 15.5px; line-height: 20.5px;
  }
</style>
</head>
<body>
<main class="brochure">
  <div class="panel panel--left"></div>
  <div class="panel panel--middle"></div>
  <div class="panel panel--right"></div>

  <div class="photo" role="img" aria-label="Photo of a therapist with a clipboard talking with a young patient seated on a treatment table"></div>

  <svg class="waves" viewBox="0 0 1200 880" aria-hidden="true">
    <defs>
      <linearGradient id="hump" x1="0" y1="1" x2="1" y2="0">
        <stop offset="0" stop-color="#4aa548"/>
        <stop offset="0.5" stop-color="#3d8c44"/>
        <stop offset="1" stop-color="#2e6e3e"/>
      </linearGradient>
    </defs>
    <path d="M800,378 Q1000,352 1200,404 L1200,880 L800,880 Z" fill="#2f7a42"/>
    <path d="M0,637 C140,662 300,650 400,612 C470,588 530,560 562,540 C480,630 300,740 0,762 Z" fill="var(--green-dark)"/>
    <path d="M0,776 C300,758 470,660 562,552 C660,455 730,395 800,395 C930,395 1060,560 1200,712 L1200,880 L0,880 Z" fill="url(#hump)"/>
    <path d="M400,690 C470,660 520,610 562,556 C650,455 730,395 800,395 L800,880 L400,880 Z" fill="var(--green-mid)" opacity="0.5"/>
    <path d="M0,769 C300,748 470,650 562,544" fill="none" stroke="#ffffff" stroke-width="5" opacity="0.9"/>
    <path d="M800,384 C940,386 1080,560 1200,706" fill="none" stroke="#ffffff" stroke-width="5" opacity="0.85"/>
  </svg>

  <h1 class="programs-title">2 OFFICE LOCATIONS<br>SPECIALTY PROGRAMS</h1>

  <ul class="program-list program-list--left">
    <li>Work Injury</li>
    <li>Motor Vehicle Accidents</li>
    <li>Spanish Speaking</li>
    <li>Neck and Back Pain</li>
    <li>Shoulder Pain</li>
  </ul>

  <div class="offices">
    <address class="office office--fernvale">
      <span class="office-name">Fernvale</span>
      3715 Tillman Parkway<br>Fernvale NY 10592<br>718-904-3218
    </address>
    <address class="office office--dalton">
      <span class="office-name">Dalton Heights</span>
      4871 Pinecrest Blvd<br>Dalton Heights NY 10592<br>718-582-0147
    </address>
  </div>

  <ul class="program-list program-list--middle">
    <li>Rotator Cuff Disorder</li>
    <li>Bursitis</li>
    <li>Hip Pain</li>
    <li>Knee, Ankle, and Foot Pain</li>
    <li>Neck and Back Pain</li>
    <li>Post Operative Care Including<br>Spine, Shoulder, Knee,<br>Total Joint Replacement</li>
  </ul>

  <div class="brand">
    <span class="brand-mark"></span>
    <span class="brand-name">Meadowlark Physical Therapy,<br>Chiropractic, and Acupuncture</span>
  </div>
  <p class="website">www.meadowlarkptrehab.com</p>

  <h2 class="contact-title">CONTACT OUR FERNVALE<br>&amp; DALTON HEIGHTS<br>CHIROPRACTORS TODAY!</h2>
  <p class="contact-body">With two locations to serve you, Dr. Warren Ellsworth, Dr. Martin<br>Kessler and Dr. Paul Redmond want to provide convenient and helpful<br>care. The chiropractors work with local medical professionals to ensure<br>your healthy progress. We want to be part of your team, so please<br>call us today in the Fernvale office at 718-904-3218 or in Dalton Heights<br>office at 718-582-0147. We are offering a free consultation for new<br>patients and hope to hear from you.</p>
</main>
</body>
</html>
```